Veltrane Group Business Card Design

The CEO is looking for a new trendy look for his business card.
You can stay with current branding or come up with something new/creative. It can be 3D, including Medical Office buildings. You can use our logo in a variety of colors. Please include name, title, company name, company website, email address, cell number

Target Market(s)

Real Estate Development and Construction

Industry/Entity Type

Health care real estate

Contact Information for Business Card

Rohesh Kamdar, CEO M-604.781.2249 E-roheshkamdar@veltrane.com Address:4180 Lindqvist Ave, Tampa, FL 33482 www.veltrane.com

Font styles to use
Other font styles liked:
• Be creative

Requirements
Must have
• Creative, trendy look
Nice to have
• Please go to our website to get a feel- www. veltrane.com
Should not have
• small fonts

```html
<!DOCTYPE html>
<html lang="en">
<head>
<meta charset="utf-8">
<title>Veltrane Group Business Card</title>
<link rel="stylesheet" href="https://fonts.googleapis.com/css2?family=Montserrat:wght@400;500;600&family=Poppins:wght@400;500;800&display=swap">
<style>
  :root {
    --brand-red: #b31d2a;
    --brand-red-dark: #a51a26;
    --brand-navy: #1d2f55;
    --paper: #ffffff;
    --ink-grey: #6b6b6f;
    --line-grey: #e6e6e8;
    --backdrop: #2b2c2f;
  }
  * { box-sizing: border-box; margin: 0; padding: 0; }
  html, body { width: 1200px; height: 952px; overflow: hidden; }
  body {
    background: var(--backdrop);
    display: flex;
    flex-direction: column;
    align-items: center;
    justify-content: center;
    gap: 48px;
    font-family: "Poppins", sans-serif;
  }
  .card {
    position: relative;
    width: 700px;
    height: 400px;
    overflow: hidden;
    box-shadow: 0 10px 30px rgba(0,0,0,.45);
  }

  /* Front */
  .card--front { background: var(--brand-red); }
  .front__drawing {
    position: absolute;
    inset: 0;
    background: linear-gradient(135deg, rgba(0,0,0,0) 20%, rgba(120,10,20,.28) 55%, rgba(0,0,0,0) 90%);
  }
  .front__wordmark {
    position: absolute;
    left: 0; right: 0; top: 120px;
    text-align: center;
    color: var(--paper);
    font-weight: 800;
    font-size: 68px;
    letter-spacing: -1px;
    line-height: 1;
  }
  .front__wordmark-sub {
    display: block;
    font-size: 34px;
    letter-spacing: 1px;
    margin-top: 6px;
  }
  .front__band {
    position: absolute;
    left: 0; right: 0; bottom: 0;
    height: 72px;
    background: var(--brand-navy);
    display: flex;
    align-items: center;
    justify-content: center;
    gap: 28px;
    color: var(--paper);
    font-size: 24px;
  }
  .front__band span::before {
    content: "";
    display: inline-block;
    width: 7px; height: 7px;
    border-radius: 50%;
    background: var(--paper);
    margin-right: 10px;
    vertical-align: middle;
  }

  /* Back */
  .card--back { background: var(--paper); }
  .back__drawing {
    position: absolute;
    right: 40px; bottom: 0;
    width: 380px; height: 230px;
    background: radial-gradient(ellipse at center, var(--line-grey) 0%, rgba(255,255,255,0) 70%);
  }
  .back__wordmark {
    position: absolute;
    left: 56px; top: 44px;
    color: var(--brand-red);
    font-weight: 800;
    font-size: 44px;
    letter-spacing: -1px;
    line-height: 1;
  }
  .contact-list {
    position: absolute;
    left: 56px; top: 150px;
    list-style: none;
    font-size: 17px;
    color: var(--ink-grey);
  }
  .contact-list li {
    display: flex;
    align-items: flex-start;
    gap: 10px;
    margin-bottom: 9px;
    line-height: 1.25;
  }
  .contact-icon { flex: none; width: 20px; height: 20px; margin-top: 1px; }
  .person {
    position: absolute;
    right: 92px; top: 270px;
    text-align: right;
    font-family: "Montserrat", sans-serif;
  }
  .person__name {
    font-size: 30px;
    font-weight: 500;
    letter-spacing: 2px;
    color: var(--brand-navy);
  }
  .person__name strong { color: var(--brand-red); font-weight: 600; }
  .person__title {
    font-size: 18px;
    color: var(--ink-grey);
    letter-spacing: 1px;
  }
  .person__mark {
    position: absolute;
    right: 0; top: 270px;
    width: 72px; height: 62px;
    background: var(--brand-red);
  }
</style>
</head>
<body>

  <section class="card card--front">
    <div class="front__drawing" role="img" aria-label="Faint architectural line drawing of a building"></div>
    <div class="front__wordmark">Veltrane<span class="front__wordmark-sub">group</span></div>
    <div class="front__band">
      <span>Real Estate</span>
      <span>Development</span>
      <span>Construction</span>
    </div>
  </section>

  <section class="card card--back">
    <div class="back__drawing" role="img" aria-label="Faint wireframe drawing of a medical office building"></div>
    <div class="back__wordmark">Veltrane<br><span style="font-size:26px">group</span></div>

    <ul class="contact-list">
      <li>
        <svg class="contact-icon" viewBox="0 0 20 20"><rect width="20" height="20" rx="3" fill="var(--brand-red)"/><path d="M10 4a4 4 0 0 0-4 4c0 3 4 8 4 8s4-5 4-8a4 4 0 0 0-4-4zm0 5.5a1.5 1.5 0 1 1 0-3 1.5 1.5 0 0 1 0 3z" fill="#fff"/></svg>
        <span>4180 Lindqvist Ave, Tampa<br>FL 33482</span>
      </li>
      <li>
        <svg class="contact-icon" viewBox="0 0 20 20"><rect width="20" height="20" rx="3" fill="var(--brand-navy)"/><path d="M6 4.5l2.5 0 1 3-1.5 1.2a8 8 0 0 0 3.3 3.3l1.2-1.5 3 1v2.5c0 .6-.5 1-1 1A10 10 0 0 1 5 5.5c0-.5.4-1 1-1z" fill="#fff"/></svg>
        <span>604.781.2249</span>
      </li>
      <li>
        <svg class="contact-icon" viewBox="0 0 20 20"><rect width="20" height="20" rx="3" fill="var(--brand-navy)"/><rect x="4" y="6" width="12" height="8" fill="none" stroke="#fff" stroke-width="1.4"/><path d="M4 6l6 5 6-5" fill="none" stroke="#fff" stroke-width="1.4"/></svg>
        <span>roheshkamdar@veltrane.com</span>
      </li>
      <li>
        <svg class="contact-icon" viewBox="0 0 20 20"><rect width="20" height="20" rx="3" fill="var(--brand-navy)"/><path d="M7 5l7 5-3 .6 2 3.6-1.4.8-2-3.6L7 13z" fill="#fff"/></svg>
        <span>www.veltrane.com</span>
      </li>
    </ul>

    <div class="person">
      <div class="person__name">ROHESH <strong>KAMDAR</strong></div>
      <div class="person__title">CEO</div>
    </div>
    <div class="person__mark"></div>
  </section>

</body>
</html>
```